Innovative tech company looking for a new look for business card

We need a business card revamp- our current design is amazingly dated and in need of a new vision. The Delta is logo that is used, but other than that and the company name - we are open to everything- red is the color of choice typically due to delta. QV is a National credit reporting agency servicing lending institutions for more than 24 years.

***We want a minimal, clean design, we want to move away from the harsh- red, black and white feel. The files uploaded are to show what we are currently using and exactly what we want to move AWAY from.

Thanks you to all!

We are looking for a "lighter" feel more "plumwick-esque." We want to move away from the harsh black , white, and red. The files I uploaded were more to show what we currently have and really want to move away from. I am going to edit the brief to be sure this is expressed.

Reason: Still looking for options....

Reason: Still looking for more designs -

```html
<!DOCTYPE html>
<html lang="en">
<head>
<meta charset="utf-8">
<title>Quill Vantage – Business Card</title>
<link rel="stylesheet" href="https://fonts.googleapis.com/css2?family=Open+Sans:ital,wght@0,400;0,600;0,700;0,800;1,400&display=swap">
<style>
  :root {
    --canvas: #f1eeec;
    --paper: #fdfcfb;
    --ink: #33373d;
    --ink-soft: #6a7078;
    --band: #6b7480;
    --band-line: #8a929c;
    --accent: #e86a5f;
    --accent-soft: #f3a69e;
    --on-band: #ffffff;
  }
  * { box-sizing: border-box; margin: 0; padding: 0; }
  html, body {
    width: 1200px; height: 1078px; overflow: hidden;
    background: var(--canvas);
    font-family: "Open Sans", Arial, sans-serif;
    color: var(--ink);
  }
  .sheet {
    position: relative; width: 1200px; height: 1078px;
    display: flex; flex-direction: column; align-items: center;
    gap: 38px; padding-top: 40px;
  }
  .card {
    position: relative; width: 840px; height: 480px;
    background: var(--paper); overflow: hidden;
    box-shadow: 0 6px 20px rgba(60,50,45,.08);
  }

  /* brand lockup */
  .brand { position: absolute; display: flex; flex-direction: column; }
  .brand-row { display: flex; align-items: center; gap: 14px; }
  .brand-square { width: 30px; height: 30px; background: var(--accent); }
  .brand-name {
    font-weight: 600; color: var(--ink); letter-spacing: .04em;
    text-transform: uppercase;
  }
  .brand-tagline { color: var(--accent); font-style: italic; margin-top: 4px; }

  /* front */
  .front .brand { left: 70px; top: 90px; }
  .front .brand-name { font-size: 44px; }
  .front .brand-tagline { font-size: 19px; padding-left: 44px; }
  .front .band {
    position: absolute; left: 0; right: 0; top: 270px; height: 130px;
    background: var(--band);
  }
  .front .band-accent {
    position: absolute; left: 0; top: 0; width: 170px; height: 100%;
    background: var(--accent);
    border-right: 6px solid var(--paper);
  }
  .front .band-accent::after {
    content: ""; position: absolute; left: 0; right: 0; top: 50%;
    height: 4px; background: var(--accent-soft);
  }
  .front .role-block {
    position: absolute; right: 60px; top: 0; height: 100%;
    display: flex; flex-direction: column; justify-content: center;
    align-items: flex-end; color: var(--on-band);
  }
  .front .role { font-size: 50px; font-weight: 800; line-height: 1.05; }
  .front .person { font-size: 30px; font-weight: 700; }

  /* back */
  .back .contact { position: absolute; left: 70px; top: 46px; font-size: 19px; line-height: 1.3; color: var(--ink-soft); }
  .back .contact h2, .back .social h2 { font-size: 19px; font-weight: 800; color: var(--ink); }
  .back .brand { left: 70px; top: 170px; }
  .back .brand-name { font-size: 30px; }
  .back .brand-square { width: 22px; height: 22px; }
  .back .brand-tagline { font-size: 13px; padding-left: 36px; }
  .back .social { position: absolute; right: 60px; top: 130px; text-align: right; font-size: 19px; line-height: 1.3; color: var(--ink-soft); }
  .back .signature { position: absolute; right: 60px; top: 290px; text-align: right; }
  .back .signature .person { font-size: 26px; font-weight: 800; color: var(--ink); }
  .back .signature .role { font-size: 17px; color: var(--ink-soft); }
  .back .band {
    position: absolute; left: 0; right: 0; bottom: 0; height: 48px; background: var(--band);
  }
  .back .band-accent {
    position: absolute; left: 0; top: 0; width: 150px; height: 100%; background: var(--accent);
  }
</style>
</head>
<body>
<main class="sheet">

  <section class="card front" aria-label="Card front">
    <div class="brand">
      <div class="brand-row">
        <span class="brand-square"></span>
        <span class="brand-name">Quill Vantage</span>
      </div>
      <span class="brand-tagline">Advanced Credit Reporting &amp; Rescoring</span>
    </div>
    <div class="band">
      <div class="band-accent"></div>
      <div class="role-block">
        <span class="role">FOUNDER</span>
        <span class="person">Jonah Smeed</span>
      </div>
    </div>
  </section>

  <section class="card back" aria-label="Card back">
    <div class="contact">
      <h2>CONTACT US</h2>
      <p>010 555 0147</p>
      <p>hello@quillvantage.com</p>
      <p>www.quillvantage.com</p>
    </div>
    <div class="brand">
      <div class="brand-row">
        <span class="brand-square"></span>
        <span class="brand-name">Quill Vantage</span>
      </div>
      <span class="brand-tagline">Advanced Credit Reporting &amp; Rescoring</span>
    </div>
    <div class="social">
      <h2>FOLLOW US ON SOCIAL</h2>
      <p>friendsbook.com/quillvantage</p>
      <p>chirper.com/quillvantage</p>
      <p>folioboard.com/quillvantage</p>
    </div>
    <div class="signature">
      <p class="person">JONAH SMEED</p>
      <p class="role">FOUNDER</p>
    </div>
    <div class="band"><div class="band-accent"></div></div>
  </section>

</main>
</body>
</html>
```